Business Card Design

Electronic Security
Alarm Systems
CCTV
Electronic Access Control
Security System Integration

Industry/Entity Type

Business

Contact Information for Business Card

Gareth Linwood
PO Box 862
Ashgrove Qld 4071
Phone 07 38526147
Mob 0427395816

```html
<!DOCTYPE html>
<html lang="en">
<head>
<meta charset="utf-8">
<title>Kestral Business Card</title>
<link href="https://fonts.googleapis.com/css2?family=Questrial&display=swap" rel="stylesheet">
<style>
  :root{
    --backdrop:#d9d9d9;
    --card:#ffffff;
    --ink:#1f1f22;
    --orange-deep:#f06a2a;
    --orange-warm:#f7a21e;
    --orange-light:#fcc419;
    --blue-light:#a9d6ef;
    --blue-grey:#b9c6d0;
  }
  *{margin:0;padding:0;box-sizing:border-box}
  html,body{width:1200px;height:1170px;overflow:hidden}
  body{
    background:radial-gradient(circle at 50% 30%,#efefef 0%,var(--backdrop) 70%);
    font-family:"Questrial",sans-serif;
    color:var(--ink);
    position:relative;
  }
  .card{
    position:absolute;left:160px;top:325px;
    width:880px;height:520px;
    background:var(--card);
    overflow:hidden;
    box-shadow:0 6px 18px rgba(0,0,0,.25);
  }
  .card__art{position:absolute;inset:0;width:880px;height:520px}
  .brand{
    position:absolute;left:0;right:0;top:232px;
    text-align:center;
    font-size:54px;letter-spacing:3px;
    color:var(--ink);
  }
  .contact{
    position:absolute;left:90px;top:338px;
    font-size:19px;line-height:27px;letter-spacing:.5px;
  }
  .contact__label{font-weight:700;font-family:"Questrial",sans-serif;-webkit-text-stroke:.5px var(--ink)}
  .services{
    position:absolute;right:52px;top:330px;
    text-align:right;list-style:none;
    font-size:21px;line-height:27px;letter-spacing:.4px;
  }
</style>
</head>
<body>
  <article class="card">
    <svg class="card__art" viewBox="0 0 880 520" aria-hidden="false">
      <defs>
        <linearGradient id="facetOrange" x1="0" y1="0" x2="1" y2="1">
          <stop offset="0" stop-color="var(--orange-light)"/>
          <stop offset=".5" stop-color="var(--orange-warm)"/>
          <stop offset="1" stop-color="var(--orange-deep)"/>
        </linearGradient>
        <linearGradient id="facetBlue" x1="1" y1="0" x2="0" y2="1">
          <stop offset="0" stop-color="var(--blue-grey)"/>
          <stop offset=".6" stop-color="var(--blue-light)"/>
          <stop offset="1" stop-color="#c3e3f5"/>
        </linearGradient>
      </defs>
      <polygon role="img" aria-label="Orange faceted corner decoration"
        points="0,0 210,0 165,45 95,45 0,175" fill="url(#facetOrange)"/>
      <polygon role="img" aria-label="Orange faceted corner decoration"
        points="680,0 880,0 880,185 845,150 840,65 790,55" fill="url(#facetOrange)"/>
      <polygon role="img" aria-label="Pale blue faceted background panel"
        points="880,185 880,520 370,520 470,425 560,430 600,330 700,260 800,170" fill="url(#facetBlue)" opacity=".9"/>
    </svg>

    <div class="brand">KESTRAL</div>

    <div class="contact">
      <p><span class="contact__label">Address:</span> Gareth Linwood</p>
      <p>PO Box 862</p>
      <p>Ashgrove Qld 4071</p>
      <p><span class="contact__label">Phone:</span> 07 38526147</p>
      <p><span class="contact__label">Mob:</span> 0427395816</p>
    </div>

    <ul class="services">
      <li>Electronic Security</li>
      <li>Alarm Systems</li>
      <li>CCTV</li>
      <li>Electronic Access Control</li>
      <li>Security System Integration</li>
    </ul>
  </article>
</body>
</html>
```